Wordpress - For IT, Cloud/Hosting, Residential/Commercial Construction Services

We are a holding company for service companies. We want the current Wordpress site modified or a new wordpress site completed. We want this site to be the parent website, that then has pull down menus linking to our other website (currently http://brightwallfix.com, http://q7v.host and would like it to be easy and fluid as we acquire more companies as we have with TKLS, Inc., B&J Construction, Brightwall Fix etc. Model after sites like Pemrose.com, Tallowbine.com, QDV.com,.vanterelm.com

------

The parent is the main site q7v Corp. Below that are sub corps and DBAs. q7v Corp stands for Quick 7 Venture Corp. q7v Offers IT manages services, 24x7 support, Monitoring NOC, Remote Hands, Onsite support services. We have acquired TKLS, Inc, B & J Construction, BrightwallFix.com. We plan to acquire/spin up many companies that offer service, support and installation offerings and will all be known as an q7v Corp Company for branding purposes. We recently had our logo done, but then ran it through 3d glass as we like the look better than the original works. We have original files in vector, but not the 3D galss door render.

Target Market(s)

IT Server and Desktop Support. Construction. Mold Remediation. Mergers and Acquisitions.

Industry/Entity Type

It Company

Coding

Coded - Design and coding required

Font styles to use
Sans Serif

Colors
0792cd

Requirements
Must have
• Clean interface. Modern design. Mobile device and multi browser support. Must be for Wordpress. Job posting with resume submission module.Hook to our Web hosting portal (Tormund) API into VexaLine Reseller portal, customer portal to allow payments to their account etc.. Easy to edit. Easy to add to, Press Release Section, Investor Relations etc.
Should not have
• Slow loading. Played out design. Over use of stock images. Copied from a competitor or something point to such.

```html
<!DOCTYPE html>
<html lang="en">
<head>
<meta charset="utf-8">
<title>Q7V Corp — Cloud &amp; Hosting</title>
<link rel="stylesheet" href="https://fonts.googleapis.com/css2?family=Poppins:wght@300;400;500;600;700&family=Open+Sans:ital,wght@0,400;0,600;1,400&display=swap">
<style>
:root{
  --brand:#0792cd;
  --navy:#1d4fa6;
  --deep:#0b2d6b;
  --teal:#15b1d6;
  --ink:#222;
  --muted:#666;
  --footer:#1273c4;
  --dark:#141414;
}
*{margin:0;padding:0;box-sizing:border-box}
html,body{width:1200px;height:3879px;overflow:hidden}
body{position:relative;font-family:'Poppins',sans-serif;color:var(--ink);background:#fff}
.abs{position:absolute}
/* header */
.header{left:0;top:0;width:1200px;height:108px;background:#fff;box-shadow:0 2px 6px rgba(0,0,0,.08);z-index:3}
.logo{left:145px;top:20px;font-weight:700;color:var(--navy);line-height:1}
.logo .mark{font-size:40px;letter-spacing:-1px}
.logo .sub{font-size:15px;letter-spacing:9px;display:block;margin-top:2px}
.contact-top{top:18px;font-size:17px;color:var(--navy);display:flex;align-items:center;gap:10px}
.contact-top .ring{width:36px;height:36px;border:2px solid var(--navy);border-radius:50%;display:flex;align-items:center;justify-content:center}
.nav{right:145px;top:70px;display:flex;gap:30px;font-size:17px;font-weight:500;color:#222}
/* hero */
.hero{left:0;top:108px;width:1200px;height:670px;background:linear-gradient(180deg,#0d1f4d 0%,#23407e 45%,#2a4f8c 70%,#182c5a 100%)}
.hero-title{left:0;top:330px;width:1200px;text-align:center;color:#fff;font-weight:700;font-size:60px;line-height:68px;text-shadow:0 2px 8px rgba(0,0,0,.4)}
.hero-btn{left:508px;top:488px;width:184px;height:50px;border:3px solid #fff;border-radius:25px;color:#fff;font-weight:600;font-size:17px;display:flex;align-items:center;justify-content:center}
.dots{left:566px;top:703px;display:flex;gap:8px}
.dots span{width:15px;height:15px;border-radius:50%;border:2px solid #fff}
.dots span.on{background:#fff}
.wave{left:0;top:700px;width:1200px;height:90px}
/* welcome */
.welcome-h{left:145px;top:895px;font-size:34px;font-weight:400;letter-spacing:.5px}
.welcome-h b{color:var(--navy);font-weight:700}
.welcome-p{left:145px;width:450px;font-family:'Open Sans',sans-serif;font-size:13.5px;line-height:25px;color:#333}
.btn-outline{left:145px;top:1198px;width:116px;height:34px;border:2px solid #222;border-radius:17px;font-size:12px;font-weight:600;display:flex;align-items:center;justify-content:center}
.welcome-photo{left:668px;top:890px;width:410px;height:375px;background:#fff;box-shadow:0 4px 14px rgba(0,0,0,.25)}
.welcome-photo div{position:absolute;left:-16px;top:-16px;width:410px;height:375px;background:linear-gradient(135deg,#3a4b5e,#8397a9 55%,#2a3542)}
/* section titles */
.sec-title{left:0;width:1200px;text-align:center;font-size:38px;font-weight:400;letter-spacing:.5px}
.sec-title b{font-weight:700}
/* services */
.card{color:#fff;text-align:center}
.card h3{font-size:21px;font-weight:700;margin-bottom:14px}
.card p{font-family:'Open Sans',sans-serif;font-size:13px;line-height:24px;padding:0 38px}
.card .more{display:inline-block;margin-top:18px;border:2px solid #fff;border-radius:16px;padding:5px 22px;font-size:12px}
.card svg{display:block;margin:0 auto 22px}
.c-blue{background:linear-gradient(160deg,#2a95d9,#1a76c3)}
.c-teal{background:linear-gradient(160deg,#25bde0,#0fa1cc)}
/* news */
.news{width:293px;height:375px;background:#fff;border:1px solid #ddd;box-shadow:0 1px 6px rgba(0,0,0,.12)}
.news .ph{height:185px}
.news .date{position:absolute;left:18px;top:205px;background:var(--deep);color:#fff;font-size:12px;padding:6px 12px}
.news h4{position:absolute;left:18px;top:250px;font-size:18px;font-weight:500}
.news p{position:absolute;left:18px;top:290px;width:255px;font-family:'Open Sans',sans-serif;font-size:13px;line-height:22px;color:#555}
/* testimonials */
.testi{left:0;top:2652px;width:1200px;height:455px;background:linear-gradient(180deg,#1b1b1b,#0f0f0f)}
.testi-h{left:0;top:2745px;width:1200px;text-align:center;color:#fff;font-size:37px;font-weight:700}
.avatar{left:270px;top:2842px;width:175px;height:175px;border-radius:50%;border:5px solid #3a7bd5;background:linear-gradient(160deg,#4a5a6a,#98a4ac)}
.quote{left:510px;top:2850px;width:470px;color:#fff;font-family:'Open Sans',sans-serif;font-style:italic;font-size:15.5px;line-height:27px}
.q-mark{font-family:Georgia,serif;font-size:70px;color:#888;line-height:1}
.author{left:512px;top:2945px;color:#fff;font-size:17px;line-height:27px;font-weight:500}
.arrow{color:#fff;font-size:40px}
/* partners */
.badge{top:3277px;width:174px;height:78px;border:1px solid #ddd;display:flex;align-items:center;justify-content:center}
.badge span{width:110px;height:24px;background:#cfd3d8;border-radius:3px}
/* footer */
.footer{left:0;top:3448px;width:1200px;height:431px;background:var(--footer);color:#fff}
.f-h{font-size:17px;font-weight:600;letter-spacing:.3px}
.f-t{font-family:'Open Sans',sans-serif;font-size:13.5px;line-height:21px}
.f-links{font-family:'Open Sans',sans-serif;font-size:14px;line-height:22px}
.soc{display:flex;align-items:center;gap:10px;font-family:'Open Sans',sans-serif;font-size:14px;margin-bottom:11px}
.soc i{width:24px;height:24px;border:2px solid #fff;border-radius:50%}
.email{width:275px;height:32px;background:#fff;border-radius:16px;color:#888;font-size:11px;padding:9px 16px}
.sub-btn{width:104px;height:32px;background:#111;color:#fff;border-radius:16px;font-size:11px;font-weight:600;display:flex;align-items:center;justify-content:center}
.copy{left:0;top:3830px;width:1200px;text-align:center;color:#fff;font-size:14px}
</style>
</head>
<body>

<header class="abs header">
  <div class="abs logo"><span class="mark">Q7V</span><span class="sub">CORP</span></div>
  <div class="abs contact-top" style="left:595px">
    <span class="ring"><svg width="16" height="16" viewBox="0 0 24 24" fill="none" stroke="#1d4fa6" stroke-width="2.2"><path d="M5 3h4l2 5-2.5 1.5a11 11 0 0 0 6 6L16 13l5 2v4a2 2 0 0 1-2 2A17 17 0 0 1 3 5a2 2 0 0 1 2-2z"/></svg></span>+1 555-014-2290
  </div>
  <div class="abs contact-top" style="left:826px">
    <span class="ring"><svg width="16" height="14" viewBox="0 0 24 20" fill="none" stroke="#1d4fa6" stroke-width="2.2"><rect x="2" y="2" width="20" height="16" rx="2"/><path d="M2 4l10 7 10-7"/></svg></span>info@q7vcorp.com
  </div>
  <nav class="abs nav"><span>HOME</span><span>ABOUT US</span><span>COMPANY &#8964;</span><span>SERVICES</span><span>CONTACT US</span></nav>
</header>

<section>
  <div class="abs hero" role="img" aria-label="Hero photo: person in a data centre with server racks and city lights"></div>
  <h1 class="abs hero-title">Q7V CORP<br>CLOUD &amp; HOSTING</h1>
  <div class="abs hero-btn">GET MORE INFO</div>
  <div class="abs dots"><span class="on"></span><span></span><span></span></div>
  <svg class="abs wave" viewBox="0 0 1200 90" preserveAspectRatio="none"><path d="M0 20 Q600 80 1200 20 L1200 90 L0 90Z" fill="#fff"/><path d="M0 20 Q600 80 1200 20" stroke="#1d4fa6" stroke-width="8" fill="none"/></svg>
</section>

<section>
  <h2 class="abs welcome-h">WELCOME TO <b>Q7V CORP</b></h2>
  <p class="abs welcome-p" style="top:960px">q7v Corp is a Norvane and Tallowbine IT Solution Provider. We provide support for Desktops, Laptops, Tablets, Mobile Devices, Networking, WIFI, Server, Design and more by providing Remote and OnSite Support Services.</p>
  <p class="abs welcome-p" style="top:1072px">q7v Corp (Quick 7 Venture) Full service one stop shop service provider. Our CEO and Founder Colin Ashby has been working with Tallowbine Solutions all the way back to TB Dos and all the way to Tallowbine's full solution offerings of today.</p>
  <div class="abs btn-outline">READ MORE</div>
  <div class="abs welcome-photo"><div role="img" aria-label="Photo of two engineers with a laptop in a server room"></div></div>
</section>

<h2 class="abs sec-title" style="top:1352px">OUR <b>SERVICES</b></h2>
<section>
  <div class="abs card c-blue" style="left:0;top:1513px;width:300px;height:427px;padding-top:50px">
    <svg width="90" height="90" viewBox="0 0 90 90" fill="none" stroke="#fff" stroke-width="3"><rect x="10" y="40" width="34" height="24"/><path d="M4 66h82M70 66v20M62 30a8 8 0 1 0 0-1M56 66V44h14l4 22"/></svg>
    <h3>IT SERVICES</h3>
    <p>Sed ut perspiciatis unde omnis iste natus error sit voluptatem accusantium doloremque laudantium, totam rem aperiam, eaque ipsa quae ab illo inventore veritatis et quasi</p>
    <span class="more">Read More</span>
  </div>
  <div class="abs card c-teal" style="left:300px;top:1480px;width:300px;height:430px;padding-top:40px">
    <svg width="90" height="90" viewBox="0 0 90 90" fill="none" stroke="#fff" stroke-width="3"><path d="M45 6l14 6v10c0 9-6 14-14 17-8-3-14-8-14-17V12z"/><rect x="8" y="50" width="30" height="20"/><rect x="52" y="50" width="30" height="20"/><path d="M45 39v12M23 70v10M67 70v10M15 80h60"/></svg>
    <h3>CLOUD &amp; HOSTING</h3>
    <p>Sed ut perspiciatis unde omnis iste natus error sit voluptatem accusantium doloremque laudantium, totam rem aperiam, eaque ipsa quae ab illo inventore veritatis et</p>
    <span class="more">Read More</span>
  </div>
  <div class="abs card c-blue" style="left:600px;top:1513px;width:300px;height:430px;padding-top:50px">
    <svg width="90" height="90" viewBox="0 0 90 90" fill="none" stroke="#fff" stroke-width="3"><rect x="30" y="10" width="30" height="74"/><rect x="8" y="40" width="22" height="44"/><rect x="60" y="30" width="22" height="54"/><path d="M38 20h4M48 20h4M38 32h4M48 32h4M38 44h4M48 44h4M38 56h4M48 56h4"/></svg>
    <h3>COMMERCIAL</h3>
    <p>Sed ut perspiciatis unde omnis iste natus error sit voluptatem accusantium doloremque laudantium, totam rem aperiam, eaque ipsa quae ab illo inventore veritatis</p>
    <span class="more">Read More</span>
  </div>
  <div class="abs card c-teal" style="left:900px;top:1480px;width:300px;height:430px;padding-top:40px">
    <svg width="90" height="90" viewBox="0 0 90 90" fill="none" stroke="#fff" stroke-width="3"><circle cx="45" cy="34" r="20"/><circle cx="45" cy="34" r="7"/><path d="M35 54v14h20V54M37 74h16M40 80h10"/></svg>
    <h3>CONSTRUCTION</h3>
    <p>Sed ut perspiciatis unde omnis iste natus error sit voluptatem accusantium doloremque laudantium, totam rem aperiam, eaque ipsa quae ab illo inventore veritatis et quasi</p>
    <span class="more">Read More</span>
  </div>
</section>

<h2 class="abs sec-title" style="top:2046px">LATEST <b>NEWS</b></h2>
<section>
  <article class="abs news" style="left:143px;top:2160px">
    <div class="ph" role="img" aria-label="Photo of a hand touching a digital interface" style="background:linear-gradient(135deg,#0d2244,#2f6aa6 60%,#0a1a33)"></div>
    <span class="date">&#128197; October 17, 2018</span><h4>Quis autem vel eum iure</h4>
    <p>Sed ut perspiciatis unde omnis iste natus error sit voluptatem accusantium doloremque lauantium</p>
  </article>
  <article class="abs news" style="left:453px;top:2160px">
    <div class="ph" role="img" aria-label="Photo of a business handshake at a desk" style="background:linear-gradient(135deg,#8a7b6c,#d9d2c8 55%,#6b5d50)"></div>
    <span class="date">&#128197; October 17, 2018</span><h4>Quis autem vel eum iure</h4>
    <p>Sed ut perspiciatis unde omnis iste natus error sit voluptatem accusantium doloremque lauantium</p>
  </article>
  <article class="abs news" style="left:763px;top:2160px">
    <div class="ph" role="img" aria-label="Photo of cloud computing icons over a keyboard" style="background:linear-gradient(135deg,#3c5574,#aab9ca 55%,#2c3d55)"></div>
    <span class="date">&#128197; October 17, 2018</span><h4>Quis autem vel eum iure</h4>
    <p>Sed ut perspiciatis unde omnis iste natus error sit voluptatem accusantium doloremque lauantium</p>
  </article>
</section>

<section>
  <div class="abs testi" role="img" aria-label="Dark office background"></div>
  <h2 class="abs testi-h">CLIENT TESTIMONIALS</h2>
  <span class="abs arrow" style="left:152px;top:2878px">&#8249;</span>
  <span class="abs arrow" style="left:1028px;top:2878px">&#8250;</span>
  <div class="abs avatar" role="img" aria-label="Client portrait"></div>
  <span class="abs q-mark" style="left:448px;top:2830px">&ldquo;</span>
  <p class="abs quote">Aociosqu ad litora torquent per conubia nostra per inceptos hymenaeos Proin nulla arcu nonummy luctus dictum eget fermentum et lorem Nunc porta convallis pede</p>
  <span class="abs q-mark" style="left:880px;top:2905px">&rdquo;</span>
  <div class="abs author">Daniel Fenwick,<br>Q7V Corp</div>
</section>

<h2 class="abs sec-title" style="top:3183px">OUR <b>PARTNERS</b></h2>
<section>
  <span class="abs" style="left:88px;top:3290px;font-size:40px;color:#bbb">&#8249;</span>
  <div class="abs badge" style="left:133px"><span></span></div>
  <div class="abs badge" style="left:320px"><span></span></div>
  <div class="abs badge" style="left:513px"><span></span></div>
  <div class="abs badge" style="left:700px"><span></span></div>
  <div class="abs badge" style="left:890px"><span></span></div>
  <span class="abs" style="left:1085px;top:3290px;font-size:40px;color:#bbb">&#8250;</span>
</section>

<footer class="abs footer">
  <div class="abs f-h" style="left:143px;top:60px">CONTACT US</div>
  <div class="abs f-t" style="left:143px;top:100px;width:230px">
    <div style="padding-left:34px;position:relative"><svg style="position:absolute;left:0;top:2px" width="14" height="18" viewBox="0 0 14 18" fill="none" stroke="#fff" stroke-width="1.6"><path d="M7 17s6-6 6-10A6 6 0 0 0 1 7c0 4 6 10 6 10z"/><circle cx="7" cy="7" r="2"/></svg>Q7V Corp<br>61, 0 123 Road Unit #1<br>Location.</div>
    <div style="padding-left:34px;margin-top:10px;position:relative"><svg style="position:absolute;left:0;top:3px" width="14" height="14" viewBox="0 0 24 24" fill="none" stroke="#fff" stroke-width="2.4"><path d="M5 3h4l2 5-2.5 1.5a11 11 0 0 0 6 6L16 13l5 2v4a2 2 0 0 1-2 2A17 17 0 0 1 3 5a2 2 0 0 1 2-2z"/></svg>Phone : +0123456789</div>
    <div style="padding-left:34px;margin-top:9px;position:relative"><svg style="position:absolute;left:0;top:4px" width="15" height="12" viewBox="0 0 24 20" fill="none" stroke="#fff" stroke-width="2.4"><rect x="2" y="2" width="20" height="16"/><path d="M2 4l10 7 10-7"/></svg>Email : info@q7vcorp</div>
  </div>
  <div class="abs f-h" style="left:437px;top:60px">SIGN UP TO RECEIVE EMAIL</div>
  <p class="abs f-t" style="left:437px;top:102px;width:290px;font-size:11px;line-height:18px">Excepteur sint occaecat cupidatat non proident, sunt in culpa qui fermo enim ipsam voluptatem</p>
  <div class="abs email" style="left:437px;top:170px">Enter Email</div>
  <div class="abs sub-btn" style="left:437px;top:220px">SUBSCRIBE</div>
  <div class="abs f-h" style="left:780px;top:60px">QUICK LINKS</div>
  <div class="abs f-links" style="left:780px;top:103px">Home<br>About Us<br>Services<br>Company<br>Blog<br>Contact Us</div>
  <div class="abs f-h" style="left:963px;top:60px">SOCIAL</div>
  <div class="abs" style="left:963px;top:103px">
    <div class="soc"><i></i>Friendwall</div>
    <div class="soc"><i></i>Chirper</div>
    <div class="soc"><i></i>Plusring</div>
    <div class="soc"><i></i>Vidstream</div>
  </div>
</footer>
<div class="abs copy">Copyright &copy; Q7V Corp. 2018. All rights reserved.</div>
</body>
</html>
```